Vietnam Motorcycle Trip TRAVEL GUIDE!! Book Cover!

I need an adventurous book cover for a book called "THROTTLE MERIDIAN: A Wanderer's Manual for Crossing the Breadth of Vietnam". I would like people to look at the cover and think adventure and Vietnam. I want it to appeal to backpackers and people who have not travelled to Vietnam. A motorbike riding along a road in Vietnam would be ideal with some landscapes to suggest we are definitely in Vietnam. The rear cover could perhaps be one of Vietnam's tropical beaches or something else that says "this place is a paradise". It could also be something else that is quinessentially Vietnamese.

The book will be A5 Dimensions. And it will also need a printable A5 interior cover too. The interior covers can just be images. No text needed. These interior images can be motorcycle related or Vietnam related. Perhaps some images of Vietnam or some Pho or Banh Mi to give it a bit of flavour. Or a long open road with a motorbike on it.

Please leave space in the external rear, lower right hand corner for a barcode.

I've attached some images to gain inspiration from. And a sample chapter.

Colours I'd like to see on there - greens, camoflague perhaps, yellow, brown, blue.

Target Market(s)

Male backpackers aged 18-35 years old. New Zealand and Australian travellers.

Font styles to use
Serif
Sans Serif

Requirements
Must have
• Exterior and Interior covers.
Barcode space.
Title and subtitle.
Synopsis on rear cover.
Exciting title fonts - perhaps Brushstroke or something equally exciting and rugged
Nice to have
• Colours I'd like to see on there - greens, camoflague perhaps, yellow, brown, blue.

A motorbike riding on the open road of Vietnam.

Rice paddies, beaches, Korvan Conflict stuff perhaps.

A New Zealand Flag
A Vietnam Flag
Should not have
• Scenery from countries outside Southeast Asia

```html
<!DOCTYPE html>
<html lang="en">
<head>
<meta charset="utf-8">
<title>Throttle Meridian – Book Cover Spread</title>
<link rel="stylesheet" href="https://fonts.googleapis.com/css2?family=Permanent+Marker&family=Oswald:wght@500;600&family=Lato:wght@400;700&display=block">
<style>
  :root {
    --page-bg: #e4e3df;
    --cover-yellow: #f4de1e;
    --cover-yellow-deep: #e2c20e;
    --ink: #111111;
    --accent-blue: #1a63b8;
    --spine-dark: #26282b;
    --spine-text: #f4f4f4;
    --brush-olive: #8c7f4c;
    --brush-text: #fbf6e0;
    --jungle-light: #7fa83a;
    --jungle-green: #2f6b2a;
    --jungle-deep: #1d4626;
    --karst-mist: #a9b86a;
    --road-grey: #566360;
    --road-dark: #3a4845;
    --teal-shade: #235046;
    --flag-red: #d72a1e;
    --flag-blue: #1b3f8f;
    --barcode-white: #ffffff;
    --brush-font: "Permanent Marker", "Rock Salt", Impact, "Arial Black", sans-serif;
    --condensed-font: "Oswald", "Arial Narrow", Impact, sans-serif;
    --text-font: "Lato", "Helvetica Neue", Arial, sans-serif;
  }
  * { box-sizing: border-box; margin: 0; padding: 0; }
  html, body { width: 850px; height: 1200px; overflow: hidden; }
  body { background: var(--page-bg); position: relative; font-family: var(--text-font); }

  .spread {
    position: absolute; left: 0; top: 311px;
    width: 850px; height: 578px;
    box-shadow: 0 6px 18px rgba(0,0,0,.25);
  }

  /* ---------- back cover ---------- */
  .back-cover {
    position: absolute; left: 0; top: 0; width: 404px; height: 578px;
    background: radial-gradient(ellipse at 40% 35%, var(--cover-yellow) 0%, var(--cover-yellow-deep) 100%);
    overflow: hidden;
  }
  .back-landscape {
    position: absolute; left: 0; bottom: 0; width: 100%; height: 250px;
    background:
      radial-gradient(ellipse 60% 45% at 18% 62%, var(--jungle-deep) 0%, rgba(29,70,38,0) 70%),
      radial-gradient(ellipse 45% 35% at 70% 55%, var(--jungle-green) 0%, rgba(47,107,42,0) 75%),
      radial-gradient(ellipse 30% 25% at 55% 92%, var(--karst-mist) 0%, rgba(169,184,106,0) 80%),
      linear-gradient(to bottom, rgba(226,194,14,0) 0%, rgba(127,168,58,.55) 28%, var(--jungle-green) 58%, var(--jungle-deep) 100%);
  }
  .back-headline {
    position: absolute; left: 20px; right: 20px; top: 20px;
    font-weight: 400; font-size: 20.5px; line-height: 26px;
    color: var(--ink); text-align: center; text-transform: uppercase; letter-spacing: -.3px;
  }
  .back-headline strong { color: var(--accent-blue); font-weight: 700; }
  .back-body { position: absolute; left: 24px; right: 25px; top: 83px; font-size: 8.1px; line-height: 10px; color: var(--ink); }
  .back-body p + p { margin-top: 9px; }
  .reveals-heading {
    position: absolute; left: 24px; top: 162px;
    font-size: 9.6px; font-weight: 700; color: var(--accent-blue); text-transform: uppercase;
  }
  .reveals-list { position: absolute; left: 24px; right: 25px; top: 180px; list-style: none; }
  .reveals-list li {
    position: relative; padding-left: 16px; font-size: 9.4px; font-weight: 700; line-height: 11px;
    color: var(--ink); margin-bottom: 10px;
  }
  .reveals-list li::before {
    content: ""; position: absolute; left: 3px; top: 3.5px; width: 4px; height: 4px; border-radius: 50%; background: var(--ink);
  }
  .closing-line { position: absolute; left: 24px; right: 25px; top: 342px; font-size: 8.1px; line-height: 10px; color: var(--ink); }
  .paradise-tagline {
    position: absolute; left: 20px; right: 20px; top: 380px;
    font-family: var(--brush-font); font-size: 26px; line-height: 32px; color: var(--ink);
    text-align: center; text-transform: uppercase; letter-spacing: .3px; transform: skewX(-6deg);
  }
  .flags { position: absolute; left: 307px; top: 421px; display: flex; gap: 2px; }
  .flag { width: 35px; height: 22px; }
  .flag-vn { background: var(--flag-red); }
  .flag-nz { background: var(--flag-blue); }
  .site-url {
    position: absolute; right: 25px; top: 449px; font-size: 9.5px; font-weight: 700; color: var(--jungle-deep); letter-spacing: .4px;
  }
  .genre-label {
    position: absolute; left: 259px; top: 472px; font-size: 6.5px; color: #5d5a30; letter-spacing: .4px;
  }
  .barcode-area {
    position: absolute; left: 259px; top: 483px; width: 120px; height: 71px;
    background: var(--barcode-white); display: flex; align-items: center; justify-content: center;
    font-family: Georgia, serif; font-size: 5.5px; letter-spacing: 2.4px; color: #333;
  }

  /* ---------- spine ---------- */
  .spine {
    position: absolute; left: 404px; top: 0; width: 42px; height: 578px; background: var(--spine-dark);
  }
  .spine-title {
    position: absolute; left: 0; right: 0; top: 22px; margin: 0 auto; width: 20px;
    writing-mode: vertical-rl; font-family: var(--brush-font); font-size: 15px; line-height: 20px; letter-spacing: 3px; color: var(--spine-text);
  }
  .spine-subtitle {
    position: absolute; left: 0; right: 0; top: 320px; margin: 0 auto; width: 12px;
    writing-mode: vertical-rl; font-family: var(--condensed-font); font-weight: 500; font-size: 7.4px; line-height: 12px; letter-spacing: 1px;
    color: var(--spine-text); text-transform: uppercase; white-space: nowrap;
  }

  /* ---------- front cover ---------- */
  .front-cover {
    position: absolute; left: 446px; top: 0; width: 404px; height: 578px;
    background: radial-gradient(ellipse at 50% 25%, var(--cover-yellow) 0%, var(--cover-yellow-deep) 100%);
    overflow: hidden;
  }
  .front-photo {
    position: absolute; left: 0; bottom: 0; width: 100%; height: 350px;
    background:
      radial-gradient(ellipse 35% 30% at 78% 70%, var(--road-dark) 0%, rgba(58,72,69,0) 75%),
      radial-gradient(ellipse 70% 18% at 40% 28%, var(--jungle-light) 0%, rgba(127,168,58,0) 80%),
      linear-gradient(168deg, rgba(226,194,14,0) 0%, rgba(127,168,58,.75) 14%, var(--jungle-green) 28%, #6f7a62 40%, var(--road-grey) 55%, var(--road-dark) 78%, var(--teal-shade) 100%);
  }
  .front-title {
    position: absolute; left: 0; right: 0; top: 14px; text-align: center;
    font-family: var(--brush-font); font-weight: 400; line-height: 1;
  }
  .front-title .title-top { display: block; font-size: 56px; color: var(--accent-blue); letter-spacing: 1px; transform: skewX(-5deg); }
  .front-title .title-bottom { display: block; font-size: 52px; color: var(--ink); letter-spacing: 8px; margin-top: 4px; transform: skewX(-5deg); }
  .subtitle-band {
    position: absolute; left: 30px; top: 158px; width: 350px; height: 86px;
    background: var(--brush-olive); opacity: .93; transform: rotate(-8deg);
    clip-path: polygon(4% 8%, 20% 2%, 45% 6%, 70% 0%, 96% 5%, 100% 30%, 97% 55%, 100% 82%, 85% 96%, 60% 100%, 35% 94%, 10% 100%, 0% 78%, 3% 50%, 0% 25%);
  }
  .front-subtitle {
    position: absolute; left: 30px; top: 160px; width: 350px; height: 86px;
    display: flex; align-items: center; justify-content: center; text-align: center;
    font-family: var(--condensed-font); font-weight: 500; font-size: 17px; line-height: 1.1;
    text-transform: uppercase; color: var(--brush-text); transform: rotate(-8deg);
  }
  .author-name {
    position: absolute; left: 0; right: 0; top: 535px; text-align: center;
    font-family: var(--condensed-font); font-weight: 600; font-size: 22px; line-height: 28px; letter-spacing: 6px; color: var(--cover-yellow);
    text-transform: uppercase;
  }
</style>
</head>
<body>
  <div class="spread">

    <section class="back-cover">
      <div class="back-landscape" role="img" aria-label="Photo of a green valley road between limestone karst hills with two motorbikes in the distance"></div>
      <h2 class="back-headline"><strong>Travel like a pro</strong> in a country<br>where bribing cops is <strong>normal!</strong></h2>
      <div class="back-body">
        <p>Everyone knows someone who's ridden the breadth of Vietnam. What if you could do the same? For us Kiwis and Australians, it's difficult finding decent material about motorcycling in Vietnam. With so much conflicting information online and uncertainty around costs, it's no wonder people keep putting off this 1600 km road trip.</p>
        <p>Callum Ashgrove has been there and done it. In the flesh. And whether your goal is riding from Saigon to Hanoi or between beach towns, this guide is your bulletproof vest.</p>
      </div>
      <h3 class="reveals-heading">This step-by-step wanderer's manual reveals:</h3>
      <ul class="reveals-list">
        <li>How to plan your own motorcycle journey before leaving home</li>
        <li>Where and how to buy/rent a bike</li>
        <li>What types of licences and insurance you'll need</li>
        <li>How to finish your trip alive without being run over by a pig truck</li>
        <li>How to avoid getting shaken down by dodgy cops</li>
        <li>Itemized expense reports, showing this journey is possible for as little as NZ$90 per day and even as low as $50.</li>
        <li>A day-by-day riding itinerary</li>
      </ul>
      <p class="closing-line">Let's face it. None of us are getting any younger. Your own Vietnam motorcycle journey awaits. And with all the information you need in one lightweight book, what's stopping you?</p>
      <p class="paradise-tagline">This place is a paradise!</p>
      <div class="flags">
        <span class="flag flag-vn" role="img" aria-label="Vietnam flag"></span>
        <span class="flag flag-nz" role="img" aria-label="New Zealand flag"></span>
      </div>
      <p class="site-url">wanderroute.co</p>
      <p class="genre-label">TRAVEL GUIDE</p>
      <div class="barcode-area">BARCODE AREA</div>
    </section>

    <section class="spine">
      <p class="spine-title">THROTTLE MERIDIAN</p>
      <p class="spine-subtitle">A Wanderer's Manual for Crossing the Breadth of Vietnam</p>
    </section>

    <section class="front-cover">
      <div class="front-photo" role="img" aria-label="Photo of two riders on a motorbike on a mountain road in Vietnam, seen from above with green hills behind"></div>
      <h1 class="front-title">
        <span class="title-top">THROTTLE</span>
        <span class="title-bottom">MERIDIAN</span>
      </h1>
      <div class="subtitle-band"></div>
      <p class="front-subtitle">A Wanderer's Manual<br>for Crossing the<br>Breadth of Vietnam</p>
      <p class="author-name">Callum Ashgrove</p>
    </section>

  </div>
</body>
</html>
```